Hollow Mesa Farm Vault Reserve Wine Label (Front and Back)

I need to create an elite tier wine label.  I would like it to be in a light, natural color with silver or gold.  I would like it to look rich and expensive, mostly monochromatic, elegantly simple.  It will need to stand up next to wine labels that are black and charcoal colored and look like the more expensive wine of the 3.  I have attached a similar label that it will be grouped with and some instructions.
We are a winery in southeast Washington state with a reputation for fine wines and top notch terroir.  We want to present family, tradition and high value wine in the bottle.

```html
<!DOCTYPE html>
<html lang="en">
<head>
<meta charset="utf-8">
<title>Hollow Mesa Farm – Vault Reserve Label Options</title>
<link rel="stylesheet" href="https://fonts.googleapis.com/css2?family=Cinzel:wght@400;500&family=Cormorant+Garamond:wght@500&family=Open+Sans:wght@400&display=swap">
<style>
  :root {
    --backdrop: #d9d9db;
    --backdrop-light: #eeeeef;
    --heading-grey: #555558;
    --label-black: #1b1b1c;
    --label-charcoal: #3a3a3d;
    --label-white: #f4f4f3;
    --gold: #c9a23a;
    --gold-deep: #a77f1e;
    --gold-light: #e7c868;
    --ink-light: #e9e6df;
    --ink-grey: #6c6c70;
  }
  * { box-sizing: border-box; margin: 0; padding: 0; }
  html, body { width: 1200px; height: 900px; overflow: hidden; }
  body {
    background: linear-gradient(180deg, #b9b9bc 0%, var(--backdrop) 55%, var(--backdrop-light) 100%);
    font-family: "Cinzel", serif;
    position: relative;
  }
  .option-title {
    position: absolute;
    top: 40px;
    width: 240px;
    margin-left: -120px;
    text-align: center;
    font-family: "Open Sans", sans-serif;
    font-size: 22px;
    letter-spacing: 1px;
    color: var(--heading-grey);
  }
  .label {
    position: absolute;
    width: 230px;
    display: flex;
    flex-direction: column;
    align-items: center;
    text-align: center;
    box-shadow: 0 6px 18px rgba(0,0,0,.18);
  }
  .label--black { background: var(--label-black); color: var(--ink-light); }
  .label--split { background: linear-gradient(180deg, var(--label-black) 0 46%, var(--label-charcoal) 46% 100%); color: var(--ink-light); }
  .label--white { background: var(--label-white); color: var(--ink-grey); }

  .brand-mark {
    display: flex; align-items: center; justify-content: center;
    font-family: "Cinzel", serif; font-weight: 500;
    color: var(--gold);
  }
  .brand-mark--seal {
    width: 122px; height: 122px; border-radius: 50%;
    background: var(--gold);
    color: var(--label-black);
    font-size: 13px; line-height: 1.25; letter-spacing: 1px;
    margin-top: -52px;
    box-shadow: 0 3px 8px rgba(0,0,0,.45);
  }
  .brand-mark--square {
    width: 104px; height: 104px;
    border: 4px solid var(--gold);
    font-size: 13px; line-height: 1.25; letter-spacing: 1px;
  }
  .winery-name {
    font-size: 17px; line-height: 1.1; letter-spacing: .5px;
    color: var(--gold);
  }
  .region { font-size: 12.5px; letter-spacing: 1.6px; }
  .estate { font-family: "Cormorant Garamond", serif; font-size: 10.5px; letter-spacing: 1.2px; text-transform: uppercase; }
  .tier {
    width: 150px;
    font-size: 14.5px; letter-spacing: 1.8px;
    padding: 5px 0;
    position: relative;
  }
  .tier::before, .tier::after {
    content: ""; position: absolute; left: 0; right: 0; height: 1.5px;
    background: linear-gradient(90deg, transparent, var(--gold) 15%, var(--gold) 85%, transparent);
  }
  .tier::before { top: 0; }
  .tier::after { bottom: 0; }
  .tier-diamond {
    position: absolute; left: 50%; width: 5px; height: 5px; margin-left: -2.5px;
    background: var(--gold); transform: rotate(45deg);
  }
  .tier-diamond--top { top: -2px; }
  .tier-diamond--bottom { bottom: -2px; }
  .vintage { font-family: "Cormorant Garamond", serif; font-size: 12px; letter-spacing: 1.5px; }
  .varietal { font-family: "Cormorant Garamond", serif; font-size: 11px; letter-spacing: 1.2px; }
  .heritage-band {
    margin-top: auto;
    width: 100%;
    padding: 6px 0;
    background: linear-gradient(90deg, var(--gold-deep), var(--gold-light) 50%, var(--gold-deep));
    color: #3b2e10;
    font-family: "Cormorant Garamond", serif;
    font-size: 6.5px; letter-spacing: .4px; text-transform: uppercase;
  }
  .label--white .heritage-band { margin-bottom: 0; }
</style>
</head>
<body>
  <p class="option-title" style="left:287px">OPTION 1</p>
  <p class="option-title" style="left:598px">OPTION 2</p>
  <p class="option-title" style="left:892px">OPTION 3</p>

  <section class="label label--black" style="left:172px; top:250px; height:400px;">
    <div class="brand-mark brand-mark--seal">HOLLOW<br>MESA<br>FARM</div>
    <h1 class="winery-name" style="margin-top:22px">HOLLOW MESA<br>FARM</h1>
    <p class="estate" style="margin-top:12px">Estate Vineyard</p>
    <p class="region" style="margin-top:24px">HORSE HEAVEN HILLS</p>
    <p class="tier" style="margin-top:18px"><span class="tier-diamond tier-diamond--top"></span>VAULT RESERVE<span class="tier-diamond tier-diamond--bottom"></span></p>
    <p class="vintage" style="margin-top:12px">2022</p>
    <p class="varietal" style="margin-top:8px">CABERNET SAUVIGNON</p>
    <p class="heritage-band" style="margin-bottom:14px">Family stewards of the land for 5 generations</p>
  </section>

  <section class="label label--split" style="left:483px; top:230px; height:420px;">
    <h1 class="winery-name" style="margin-top:32px">HOLLOW MESA<br>FARM</h1>
    <p class="region" style="margin-top:14px">HORSE HEAVEN HILLS</p>
    <div class="brand-mark brand-mark--square" style="margin-top:20px">HOLLOW<br>MESA<br>FARM</div>
    <p class="estate" style="margin-top:14px">Estate Vineyard</p>
    <p class="tier" style="margin-top:4px; width:170px"><span class="tier-diamond tier-diamond--top"></span>VAULT RESERVE<span class="tier-diamond tier-diamond--bottom"></span></p>
    <p class="vintage" style="margin-top:12px">2022</p>
    <p class="varietal" style="margin-top:10px">CABERNET SAUVIGNON</p>
    <p class="heritage-band" style="margin-bottom:10px">Family stewards of the land for 5 generations</p>
  </section>

  <section class="label label--white" style="left:777px; top:230px; height:410px;">
    <div class="brand-mark brand-mark--square" style="margin-top:14px">HOLLOW<br>MESA<br>FARM</div>
    <h1 class="winery-name" style="margin-top:24px">HOLLOW MESA<br>FARM</h1>
    <p class="region" style="margin-top:16px">HORSE HEAVEN HILLS</p>
    <p class="estate" style="margin-top:4px">Estate Vineyard</p>
    <p class="tier" style="margin-top:18px; color:var(--ink-grey)"><span class="tier-diamond tier-diamond--top"></span>VAULT RESERVE<span class="tier-diamond tier-diamond--bottom"></span></p>
    <p class="vintage" style="margin-top:14px">2022</p>
    <p class="varietal" style="margin-top:10px">CABERNET SAUVIGNON</p>
    <p class="heritage-band" style="margin-top:14px">Family stewards of the land for 5 generations</p>
  </section>
</body>
</html>
```